Bright, Bold Sydney Tutoring Business Flyer Advertisment

Lumora is an up and coming tutoring business located on Sydney's Upper North Shore catering to school students of all ages. We need a flyer designed for notice boards and letter box drops to attract new clients. Our tutors are mostly university education students who are fresh, dedicated and passionate about their areas of teaching. The flyer should exhibit a bright, bold, modern, clean cut style which would appeal to both students and parents. I have attached our logo (the flyer could reflect this colour scheme), and a PDF which outlines the information we would like to appear on the flyer. This is not set in stone, but designed to act as an extremely loose guide for your creativity !

Target Market(s)

Affluent School Students and Parents

Industry/Entity Type

Tutoring

Requirements
Must have
• Logo, $10 offer, company description.
Nice to have
• Grabbing headlines to attract new clients, such as "Feeling overwhelmed at school?". We are looking for an eye catching, clean cut and professional design that has the colours to attract kids and the tone to attract parents.

```html
<!DOCTYPE html>
<html lang="en">
<head>
<meta charset="utf-8">
<title>Lumora Tutoring Flyer</title>
<link rel="stylesheet" href="https://fonts.googleapis.com/css2?family=Arimo:wght@400;700&display=swap">
<style>
:root{
  --sky:#6fd2f4;
  --sky-deep:#4fc3ee;
  --pink:#f7a8d8;
  --pink-soft:#fbe3f1;
  --ink:#1d1d1d;
  --white:#ffffff;
}
*{margin:0;padding:0;box-sizing:border-box}
html,body{width:862px;height:1200px;overflow:hidden;background:var(--white)}
.flyer{
  position:relative;width:862px;height:1200px;overflow:hidden;
  font-family:"Arimo",Arial,sans-serif;
  background:linear-gradient(180deg,#ffffff 0%,#fdf3f9 35%,#f9e6f2 57%,#ffffff 57.1%);
}
.accent-block{position:absolute;left:0;top:106px;width:62px;height:96px;background:var(--pink)}
.headline{
  position:absolute;left:72px;top:108px;
  color:var(--sky);font-weight:700;font-size:49px;line-height:52px;
  text-transform:uppercase;letter-spacing:0.5px;
}
.question{position:absolute;left:86px;font-weight:700;text-transform:uppercase;font-size:26px;line-height:28px}
.question--hsc{top:322px;color:var(--pink)}
.question--engage{top:440px;color:var(--sky)}
.question .hl{color:var(--pink)}
.question-bar{position:absolute;left:74px;width:4px;background:var(--pink)}
.question-bar--hsc{top:322px;height:84px}
.question-bar--engage{top:440px;height:140px;background:var(--sky)}
.photo{
  position:absolute;left:350px;top:285px;width:512px;height:398px;
  background:radial-gradient(ellipse at 60% 40%,#8fd6f2 0%,#cdebf7 40%,#f7eef3 75%,rgba(255,255,255,0) 100%);
}
.info-band{
  position:absolute;left:0;top:683px;width:862px;height:192px;background:var(--sky);
}
.info-col{
  position:absolute;top:28px;color:var(--white);font-size:22px;line-height:25px;
}
.info-col strong{font-weight:700}
.info-col--offer{left:98px;width:340px}
.info-col--tutors{left:468px;width:350px}
.info-frame{position:absolute;border:2px solid var(--white)}
.info-frame--offer{left:80px;top:18px;width:0;height:126px;border-width:0 0 0 2px}
.info-frame--tutors{left:448px;top:18px;width:0;height:126px;border-width:0 0 0 2px}
.brand{position:absolute;left:62px;top:940px;display:flex;flex-direction:column;align-items:center;gap:10px}
.brand-dot{width:108px;height:108px;border-radius:50%;background:var(--sky-deep)}
.brand-name{font-size:32px;font-weight:700;color:var(--ink)}
.contact{position:absolute;left:212px;top:934px;width:240px;font-size:15px;line-height:18px;color:var(--ink)}
.contact p{margin-bottom:14px}
.contact p.lines{margin-bottom:0}
.offer{
  position:absolute;right:84px;top:985px;width:300px;text-align:right;
  color:var(--pink);font-weight:700;text-transform:uppercase;font-size:21px;line-height:22px;
}
.offer-price{display:block;font-size:56px;line-height:62px;margin-top:4px}
.offer-bar{position:absolute;right:0;top:992px;width:48px;height:160px;background:var(--pink)}
</style>
</head>
<body>
<main class="flyer">
  <div class="accent-block"></div>
  <h1 class="headline">Looking to improve<br>your skills, confidence<br>and organization?</h1>

  <span class="question-bar question-bar--hsc"></span>
  <p class="question question--hsc">Feeling<br>overwhelmed<br>by the HSC?</p>

  <span class="question-bar question-bar--engage"></span>
  <p class="question question--engage">Want to<br><span class="hl">increase</span><br>your child’s<br><span class="hl">engagement</span><br>at school?</p>

  <div class="photo" role="img" aria-label="Photo of a smiling young student in glasses leaning on an open book"></div>

  <section class="info-band">
    <span class="info-frame info-frame--offer"></span>
    <p class="info-col info-col--offer">Lumora <strong>Tutoring</strong> offers <strong>one-on-one, individualized learning</strong> experiences to maximize academic <strong>development</strong>.</p>
    <span class="info-frame info-frame--tutors"></span>
    <p class="info-col info-col--tutors">Our <strong>tutors</strong> are hand selected on the basis of their qualifications, <strong>expertise</strong> and <strong>passion</strong> for inspiring young learners.</p>
  </section>

  <div class="brand">
    <span class="brand-dot"></span>
    <span class="brand-name">lumora</span>
  </div>

  <div class="contact">
    <p><strong>Contact us</strong> today to discuss how we can help make your learning goals a reality!</p>
    <p class="lines">info@lumoratutoring.com.au<br>www.lumoratutoring.com.au<br>Suite 4, 218<br>Wattle Avenue Linfield,<br>NSW 2070</p>
  </div>

  <p class="offer">Mention this advertisement to claim your trial session for just <span class="offer-price">$10!</span></p>
  <div class="offer-bar"></div>
</main>
</body>
</html>
```